Summit Ridge Business Card

Side 1: Summit Ridge Logo (logo without Maltese cross) with industrial rope rescue related theme. Our company services - TRAINING - Fire Training, Confined Space Rescue Training, Rope Rescue training, Hazmat Training, Incident Command, EMS, Pump Operations Training. Website - summitridgeexample.com.
Side 2: Summit Ridge Fire Department Logo (logo with Maltese cross) with Firefighter related theme. Company (division) services - FIELD SERVICES - Fire Department, Stand-by Rescue, Safety, EMS, Planning. "Supporting the Emergency Response Community Since 1967"

Add contact information wherever it makes since (Name, Email, Phone).
I would like it to represent the Summit Ridge Fire Department Logo as a division not as a separate entity without saying it, possibly by depicting it in the background of Side 2 instead of being a standalone picture like the logo on Side 1.

```html
<!DOCTYPE html>
<html lang="en">
<head>
<meta charset="utf-8">
<title>Summit Ridge Business Card</title>
<link rel="stylesheet" href="https://fonts.googleapis.com/css2?family=Montserrat:wght@800&family=Poppins:wght@400;500;600&display=swap">
<style>
  :root {
    --backdrop: #3b3b3d;
    --card: #1d1d1f;
    --red: #e63a1f;
    --red-bright: #ee1c24;
    --white: #ffffff;
    --grey: #8a8a8a;
  }
  * { box-sizing: border-box; margin: 0; padding: 0; }
  html, body { width: 1200px; height: 689px; overflow: hidden; }
  body {
    background: var(--backdrop);
    font-family: "Poppins", sans-serif;
    color: var(--white);
    position: relative;
  }
  .card {
    position: absolute;
    width: 540px;
    height: 309px;
    background: var(--card);
    border-radius: 18px;
    overflow: hidden;
    box-shadow: 0 14px 30px rgba(0,0,0,.45);
  }
  .card--front { left: 36px; top: 48px; }
  .card--back { left: 624px; top: 332px; }

  .band {
    position: absolute;
    left: 0; right: 0; bottom: 0;
    height: 48px;
    background: var(--red);
    display: flex;
    align-items: center;
    justify-content: center;
    font-size: 15px;
    font-weight: 500;
    letter-spacing: .2px;
  }

  .section-title {
    font-family: "Montserrat", sans-serif;
    font-weight: 800;
    color: var(--red);
    font-size: 17px;
    letter-spacing: .6px;
    margin-bottom: 6px;
  }
  .service-list { list-style: none; }
  .service-list li {
    font-size: 13.5px;
    line-height: 19px;
    display: flex;
    align-items: center;
    gap: 8px;
  }
  .service-list li::before {
    content: "";
    width: 6px; height: 6px;
    background: var(--red);
    border-radius: 50%;
    flex: none;
  }

  /* front */
  .front-services { position: absolute; left: 30px; top: 38px; }
  .brand-name {
    position: absolute;
    right: 34px; top: 78px;
    width: 200px;
    text-align: center;
    font-family: "Montserrat", sans-serif;
    font-weight: 800;
    font-size: 27px;
    line-height: 32px;
    letter-spacing: 1px;
    color: var(--red-bright);
    text-transform: uppercase;
  }

  /* back */
  .back-services { position: absolute; left: 30px; top: 26px; }
  .divider {
    position: absolute; left: 30px; top: 156px;
    width: 70px; height: 1px; background: var(--grey);
  }
  .contact { position: absolute; left: 30px; top: 166px; }
  .contact-name {
    font-weight: 600;
    color: var(--red);
    font-size: 19px;
    margin-bottom: 4px;
  }
  .contact-line {
    display: flex; align-items: center; gap: 8px;
    font-size: 13.5px; line-height: 20px;
  }
  .contact-line svg { width: 13px; height: 13px; flex: none; }
  .division-mark {
    position: absolute;
    right: 40px; top: 36px;
    width: 176px; height: 176px;
    border: 3px solid var(--red);
    border-radius: 50%;
    display: flex; align-items: center; justify-content: center;
    text-align: center;
    font-family: "Montserrat", sans-serif;
    font-weight: 800;
    font-size: 22px;
    line-height: 26px;
    color: var(--red);
    text-transform: uppercase;
  }
  .band--tagline { font-size: 14px; font-weight: 600; }
</style>
</head>
<body>

  <section class="card card--front">
    <div class="front-services">
      <h2 class="section-title">TRAINING</h2>
      <ul class="service-list">
        <li>Fire Training</li>
        <li>Confined Space Rescue Training</li>
        <li>Rope Rescue training</li>
        <li>Hazmat Training</li>
        <li>Incident Command</li>
        <li>EMS</li>
        <li>Pump Operations Training</li>
      </ul>
    </div>
    <div class="brand-name">Summit Ridge</div>
    <div class="band">www.summitridgeexample.com</div>
  </section>

  <section class="card card--back">
    <div class="back-services">
      <h2 class="section-title">FIELD SERVICES</h2>
      <ul class="service-list">
        <li>Fire Department</li>
        <li>Stand-by Rescue</li>
        <li>Safety</li>
        <li>EMS</li>
        <li>Planning</li>
      </ul>
    </div>
    <div class="divider"></div>
    <div class="contact">
      <p class="contact-name">Daniel Hayes</p>
      <p class="contact-line">
        <svg viewBox="0 0 24 24" aria-hidden="true"><path fill="#e63a1f" d="M6.6 10.8a15.1 15.1 0 0 0 6.6 6.6l2.2-2.2a1 1 0 0 1 1-.25 11.4 11.4 0 0 0 3.6.57 1 1 0 0 1 1 1V20a1 1 0 0 1-1 1A17 17 0 0 1 3 4a1 1 0 0 1 1-1h3.5a1 1 0 0 1 1 1c0 1.25.2 2.45.57 3.57a1 1 0 0 1-.25 1z"/></svg>
        044-555 010 010
      </p>
      <p class="contact-line">
        <svg viewBox="0 0 24 24" aria-hidden="true"><rect x="2" y="5" width="20" height="14" rx="1" fill="#e63a1f"/><path d="M2 6l10 7 10-7" fill="none" stroke="#1d1d1f" stroke-width="2"/></svg>
        hello@examplemail.com
      </p>
    </div>
    <div class="division-mark">Summit<br>Ridge</div>
    <div class="band band--tagline">Supporting the Emergency Response Community Since 1967</div>
  </section>

</body>
</html>
```